418 5 minute epoxy adhesive

Hi, i need a label for the front and pack of our New Product.
Just our Vellarn Resins Logo on the front and product name. ( as above)
and Vellarn Fibreglass Logo on the back with mixing instructions on the back.

```html
<!DOCTYPE html>
<html lang="en">
<head>
<meta charset="utf-8">
<title>Vellarn 418 Series – Label Set</title>
<link rel="stylesheet" href="https://fonts.googleapis.com/css2?family=Anton&family=Rubik:ital,wght@0,700;0,800;1,800;1,900&family=Rajdhani:wght@500;700&family=Roboto+Condensed:wght@400&family=Archivo:wght@600;800&display=swap">
<style>
  :root {
    --canvas-bg: #3d3d3d;
    --label-white: #ffffff;
    --resins-blue: #0a5aae;
    --fibre-blue: #3a3f96;
    --brand-red: #e8323a;
    --ink: #1a1a1a;
    --mist: #e9edf3;
    --caption: #d8d8d8;
  }
  * { margin: 0; padding: 0; box-sizing: border-box; }
  html, body { width: 1006px; height: 1200px; overflow: hidden; }
  body { background: var(--canvas-bg); position: relative; font-family: "Rajdhani", sans-serif; }

  .label { position: absolute; background: var(--label-white); }
  .label__frame {
    position: absolute; inset: 7px;
    border: 3px solid var(--resins-blue); border-radius: 12px;
    overflow: hidden;
    background: linear-gradient(160deg, #f4f5f7 0%, #ffffff 35%, var(--mist) 100%);
  }
  .label__frame::after {
    content: ""; position: absolute; inset: 3px;
    border: 1.5px solid var(--brand-red); border-radius: 9px; pointer-events: none;
  }
  .label-size {
    position: absolute; color: var(--caption);
    font-family: "Archivo", sans-serif; font-weight: 600; font-size: 15px; letter-spacing: 1px;
  }

  /* Front label */
  .front { left: 40px; top: 400px; width: 460px; height: 368px; }
  .front .brand {
    position: absolute; top: 26px; left: 0; right: 0; text-align: center;
  }
  .front .brand__name {
    display: inline-flex; align-items: center; gap: 10px;
    font-family: "Anton", sans-serif; font-size: 38px; color: var(--brand-red); letter-spacing: 1px;
  }
  .front .brand__dot { width: 22px; height: 22px; border-radius: 50%; background: var(--resins-blue); }
  .front .brand__tagline {
    margin-top: 2px; font-family: "Archivo", sans-serif; font-weight: 800;
    font-size: 12px; letter-spacing: 2px; color: var(--resins-blue);
  }
  .front .series-band {
    position: absolute; left: 0; right: 0; top: 109px; height: 101px;
    background: var(--resins-blue); color: #fff; text-align: center;
    font-family: "Anton", sans-serif; font-size: 86px; line-height: 101px; letter-spacing: 1px;
  }
  .front .product {
    position: absolute; top: 220px; left: 0; right: 0; text-align: center;
    font-family: "Rubik", sans-serif; font-style: italic; font-weight: 900; line-height: 36px;
  }
  .front .product__time { color: var(--brand-red); font-size: 36px; }
  .front .product__type { color: var(--ink); font-size: 36px; letter-spacing: -1px; }
  .front .kit-size {
    position: absolute; bottom: 0; left: 112px; width: 210px; height: 34px;
    background: var(--brand-red); clip-path: polygon(8% 0, 92% 0, 100% 100%, 0 100%);
    color: #fff; text-align: center; line-height: 36px;
    font-family: "Rubik", sans-serif; font-style: italic; font-weight: 900; font-size: 25px;
  }
  .front .caution {
    position: absolute; bottom: 6px; right: 14px;
    font-family: "Roboto Condensed", sans-serif; font-size: 7px; color: var(--ink);
  }

  /* Back label */
  .back { left: 540px; top: 400px; width: 426px; height: 426px; }
  .back .brand {
    position: absolute; top: 30px; left: 0; right: 0; text-align: center;
    font-family: "Anton", sans-serif; font-size: 30px; color: var(--fibre-blue); letter-spacing: 1px;
    display: flex; justify-content: center; align-items: center; gap: 10px;
  }
  .back .brand__dot { width: 16px; height: 16px; background: var(--brand-red); }
  .back .series-band {
    position: absolute; left: 0; right: 0; top: 106px; height: 43px;
    background: var(--fibre-blue); color: #fff; text-align: center;
    font-family: "Rubik", sans-serif; font-weight: 800; font-size: 36px; line-height: 44px;
  }
  .back .product {
    position: absolute; top: 152px; left: 0; right: 0; text-align: center;
    font-family: "Rubik", sans-serif; font-style: italic; font-weight: 800; font-size: 25px;
    color: var(--brand-red); letter-spacing: -0.5px;
  }
  .back .description {
    position: absolute; top: 196px; left: 28px; right: 28px;
    font-family: "Rajdhani", sans-serif; font-weight: 500; font-size: 12.6px; line-height: 15.3px;
    color: #2a2a2a; text-align: justify; text-align-last: center;
  }
  .back .description strong { font-weight: 700; }
  .back .mix-ratio {
    position: absolute; left: 0; right: 0; bottom: 0; height: 39px;
    background: var(--brand-red); color: #fff; text-align: center; line-height: 40px;
    font-family: "Rajdhani", sans-serif; font-weight: 700; font-size: 14px;
  }
</style>
</head>
<body>

  <section class="label front" aria-label="Front label">
    <div class="label__frame">
      <div class="brand">
        <div class="brand__name"><span class="brand__dot"></span>VELLARN RESINS</div>
        <div class="brand__tagline">MAXXIMUM PERFORMANCE</div>
      </div>
      <div class="series-band">418 SERIES</div>
      <div class="product">
        <div class="product__time">5 MINUTE</div>
        <div class="product__type">EPOXY ADHESIVE</div>
      </div>
      <div class="kit-size">200 MLS KIT</div>
      <div class="caution">Read Caustions on the back panel</div>
    </div>
  </section>
  <div class="label-size" style="left:44px; top:788px;">100MM X 80MM</div>

  <section class="label back" aria-label="Back label">
    <div class="label__frame">
      <div class="brand"><span class="brand__dot"></span>VELLARN FIBREGLASS</div>
      <div class="series-band">418 SERIES</div>
      <div class="product">5 MINUTE EPOXY ADHESIVE</div>
      <p class="description"><strong>418 Series</strong> is a two part, free flowing, liquid epoxy adhesive with a rapid 5 minute cure time. It can be used on a wide range of materials showing excellent adhesion and superior strength. 418 Series is the perfect adhesive to have for all those general purpose projects. It is formulated to be mixed at a easy 1:1 ratio and can even have fillers added to create a thickened glue paste. With an almost endless shelf life 418 Series is the one glue that is needed in every shed in Australia. Skip the old Glumax and buy some of Vellarn's 418 Series, its a massive 630% cheaper and far superior.</p>
      <div class="mix-ratio">Mix at a ratio of 1 Part A : 1 Part B (418A : 418B)</div>
    </div>
  </section>
  <div class="label-size" style="left:544px; top:846px;">100MM X 100MM</div>

</body>
</html>
```